Automotive Accessories Business Card

Design a business template that match our new logo design and our industry.

https://www.qelmotorgear.com/

Target Market(s)

Aftermarket auto parts and accessories

Industry/Entity Type

automotive

Contact Information for Business Card

company logo

Font styles to use
Serif
Sans Serif

Colors
EB3D1F
EC4F4E
F09395
F8D3D4
FCEDEE

```html
<!DOCTYPE html>
<html lang="en">
<head>
<meta charset="utf-8">
<title>Qel Motorgear – Business Card</title>
<link href="https://fonts.googleapis.com/css2?family=Arimo:wght@400;700&display=swap" rel="stylesheet">
<style>
  :root {
    --page: #e4e2df;
    --card-white: #f6f6f6;
    --card-dark: #3b3b3d;
    --brand-red: #d2232a;
    --ink: #3a3a3c;
    --ink-soft: #555558;
    --emboss: #2f2f31;
    --rule: #6a6a6d;
  }
  * { box-sizing: border-box; margin: 0; padding: 0; }
  html, body { width: 1200px; height: 768px; overflow: hidden; }
  body {
    background: var(--page);
    font-family: "Arimo", Arial, sans-serif;
    position: relative;
  }
  .card {
    position: absolute;
    top: 229px;
    width: 540px;
    height: 310px;
    box-shadow: 0 6px 18px rgba(0,0,0,.18);
    overflow: hidden;
  }
  /* Back side */
  .card-back { left: 40px; background: var(--card-dark); }
  .card-back .brand-name {
    position: absolute; left: 0; right: 0; top: 108px;
    text-align: center;
    font-size: 46px; font-weight: 700; letter-spacing: 2px;
    color: var(--emboss);
  }
  .card-back .web {
    position: absolute; left: 0; right: 0; bottom: 58px;
    text-align: center;
    font-size: 13px; letter-spacing: 4px; color: #e8e8e8;
  }
  /* Front side */
  .card-front { left: 620px; background: var(--card-white); }
  .front-brand {
    position: absolute; right: 30px; top: 40px;
    display: flex; align-items: center; gap: 10px;
  }
  .front-brand .mark { width: 16px; height: 16px; background: var(--brand-red); }
  .front-brand .brand-name {
    font-size: 28px; font-weight: 700; letter-spacing: 1px; color: var(--brand-red);
  }
  .contact-row {
    position: absolute; left: 22px; right: 18px; top: 176px;
    display: flex; color: var(--ink);
  }
  .person { width: 190px; }
  .person .name { font-size: 19px; font-weight: 700; color: var(--brand-red); }
  .person .title { font-size: 13px; color: var(--ink-soft); margin: 3px 0 4px; }
  .person p { font-size: 13px; line-height: 17px; }
  .office {
    border-left: 1px solid var(--rule);
    padding: 12px 0 0 12px; margin-left: 8px;
    font-size: 13px; line-height: 17px;
    width: 158px;
  }
  .office .phone { display: flex; align-items: center; gap: 5px; margin-top: 6px; }
  .office svg { width: 11px; height: 11px; fill: var(--brand-red); }
  .band {
    position: absolute; left: 0; right: 0; bottom: 0; height: 14px;
    display: flex;
  }
  .band span { display: block; height: 100%; }
  .band .dark { background: var(--ink); }
  .band .red { background: var(--brand-red); }
</style>
</head>
<body>
  <section class="card card-back">
    <div class="brand-name">QEL MOTORGEAR</div>
    <div class="web">www.qelmotorgear.com</div>
  </section>

  <section class="card card-front">
    <div class="front-brand">
      <span class="mark"></span>
      <span class="brand-name">QEL MOTORGEAR</span>
    </div>

    <div class="contact-row">
      <div class="person">
        <div class="name">MARCUS ELLERY</div>
        <div class="title">Managing Director</div>
        <p>sales@qelmotorgear.com</p>
        <p>www.qelmotorgear.com</p>
      </div>
      <div class="office">
        <p>240 W. Orchard Ave. Unit B</p>
        <p>Pomona, CA, 91768</p>
        <p>United States</p>
        <p class="phone"><svg viewBox="0 0 24 24" aria-hidden="true"><path d="M6.6 10.8a15.2 15.2 0 0 0 6.6 6.6l2.2-2.2c.3-.3.7-.4 1-.2 1.1.4 2.3.6 3.6.6.6 0 1 .4 1 1V20c0 .6-.4 1-1 1A17 17 0 0 1 3 4c0-.6.4-1 1-1h3.5c.6 0 1 .4 1 1 0 1.3.2 2.5.6 3.6.1.3 0 .7-.2 1z"/></svg>1-866-555-0142</p>
      </div>
      <div class="office">
        <p>5120 Fraser Lane</p>
        <p>Burnaby, BC V5H 2K4</p>
        <p>Canada</p>
        <p class="phone"><svg viewBox="0 0 24 24" aria-hidden="true"><path d="M6.6 10.8a15.2 15.2 0 0 0 6.6 6.6l2.2-2.2c.3-.3.7-.4 1-.2 1.1.4 2.3.6 3.6.6.6 0 1 .4 1 1V20c0 .6-.4 1-1 1A17 17 0 0 1 3 4c0-.6.4-1 1-1h3.5c.6 0 1 .4 1 1 0 1.3.2 2.5.6 3.6.1.3 0 .7-.2 1z"/></svg>604-555-0187</p>
      </div>
    </div>

    <div class="band">
      <span class="dark" style="width:26%"></span>
      <span class="red" style="width:29%"></span>
      <span class="dark" style="width:30%"></span>
      <span class="red" style="width:15%"></span>
    </div>
  </section>
</body>
</html>
```